Gospel Tract titled "A Lantern Trail Toward Bright Skies."

This will be a bi-fold brochure. The design will be in the front panel of the brochure which is 4 inches wide and 8.5 inches high. This is a common brochure among Gospel tracts in the series, "A lantern trail toward bright skies ______________ ." The blank is usually a state, city, or other location. I want a "fun" image of Iowa or something representing Iowa at the bottom. A graphic representing "heaven" at the top. Perhaps a meandering road between the two. The words, "A Lantern Trail Toward Bright Skies", but be on the front somewhere. I am also open to other designs with this theme and the words "A Lantern Trail Toward Bright Skies." My suggestion is just one idea.

Target Market(s)

Non-Christians who are interested in knowing how to get to heaven

Requirements
Must have
• Something specific to the state of Iowa at the bottom: farms, state fair, cows, barns, power windmills, the capitol building, etc.
Nice to have
• I would like something bright, colorful, with a fun Iowa image at the bottom.
Should not have
• Religous symbolism....no doves, angels, crosses, etc.

```html
<!DOCTYPE html>
<html lang="en">
<head>
<meta charset="utf-8">
<title>A Lantern Trail Toward Bright Skies — Bi-fold Tract</title>
<link href="https://fonts.googleapis.com/css2?family=Cinzel:wght@400;600&family=Great+Vibes&family=Kaushan+Script&family=Bodoni+Moda:wght@400;500&family=Montserrat:ital,wght@0,400;0,600;0,700;1,400&family=Quicksand:wght@400;600&display=swap" rel="stylesheet">
<style>
:root{
  --bg:#e9e9ec;
  --royal:#1428d8;
  --deep:#0a1496;
  --navy:rgba(18,16,110,.88);
  --sky:#38a8ea;
  --cyan:#3fd8e6;
  --yellow:#f3ea2a;
  --gold:#e9d330;
  --white:#ffffff;
  --ink:#16206b;
  --grass:#5d8a2c;
  --barn:#c02a2a;
}
*{box-sizing:border-box;margin:0;padding:0}
html,body{width:889px;height:1200px;overflow:hidden;background:var(--bg)}
body{font-family:"Montserrat",sans-serif;color:var(--white);position:relative}
.spread{position:absolute;left:174px;width:540px;height:574px;overflow:hidden;box-shadow:0 8px 18px rgba(0,0,0,.25)}
.spread--outside{top:18px;background:linear-gradient(180deg,var(--deep) 0%,var(--royal) 30%,#2f6fe8 55%,var(--sky) 70%)}
.spread--inside{top:608px;background:linear-gradient(180deg,var(--royal) 0%,#1550e8 45%,#2a8ae8 70%)}
.photo{position:absolute}
.photo--farm{left:0;right:0;bottom:0;height:200px;background:linear-gradient(180deg,#9fcdf0 0%,#c7dde8 18%,var(--barn) 30%,#8d2424 42%,#7fae3a 52%,var(--grass) 75%,#3f6a1e 100%)}
.photo--gate{left:340px;top:215px;width:140px;height:195px;border-radius:50% 50% 10px 10px;background:radial-gradient(ellipse at 50% 22%,#ffffff 0%,#e6eef8 35%,#b9c9de 60%,rgba(160,190,230,0) 80%)}
.photo--fair{left:0;right:0;bottom:0;height:176px;background:linear-gradient(135deg,#5b6a5a 0%,#8c8f86 30%,#d54a7a 50%,#f0c030 62%,#2aa0d0 78%,#6b7a60 100%)}
.column{position:absolute;background:var(--navy)}
.column--back{left:32px;top:0;width:214px;height:440px}
.column--why{left:24px;top:0;width:230px;height:400px}
.center{text-align:center}
.caps{font-family:"Cinzel",serif;font-weight:600;letter-spacing:.3px}
.script{font-family:"Great Vibes",cursive;font-weight:400}
.brush{font-family:"Kaushan Script",cursive;font-weight:400}
.abs{position:absolute}
/* back panel */
.back-title{left:32px;width:214px;top:30px;font-size:11px;line-height:1.2;color:var(--gold)}
.back-script{left:32px;width:214px;top:44px;font-size:27px;line-height:1.2;color:var(--cyan)}
.back-intro{left:50px;width:178px;top:84px;font-size:5.3px;line-height:1.4}
.steps{left:32px;width:214px;top:118px;list-style:none}
.step{padding:6px 0;margin-bottom:8px;background:linear-gradient(90deg,rgba(80,110,220,.35),rgba(80,110,220,0));border-top:1px solid rgba(120,150,255,.3)}
.step h3{font-family:"Cinzel",serif;font-size:6.4px;color:var(--cyan);font-weight:600;margin-bottom:1px}
.step p{font-size:5.3px;line-height:1.4;color:#dfe4ff;padding:0 30px}
.contact{left:32px;width:214px;top:288px;font-size:6px;line-height:1.35}
.contact .lead{font-size:5.3px;color:var(--yellow);margin-bottom:9px;padding:0 40px}
.contact .row{margin-bottom:7px}
.contact svg{display:block;margin:0 auto 1px}
.quote-mark{font-family:"Bodoni Moda",serif;font-size:44px;line-height:1;color:transparent;-webkit-text-stroke:1px #4a6cff}
.back-verse{left:75px;width:128px;top:404px;font-size:5.3px;font-style:italic;line-height:1.4}
.ref{color:var(--yellow);font-style:normal;font-weight:600}
/* cover */
.cover-top{left:285px;width:240px;top:40px;font-size:11.5px;line-height:1.2;letter-spacing:3px;font-weight:400}
.cover-bright{left:290px;width:230px;top:54px;font-size:44px;line-height:1;color:var(--yellow)}
.cover-toward{left:285px;width:240px;top:104px;font-size:8px;line-height:1.2;letter-spacing:3px;font-weight:400;color:#dde6ff}
.cover-skies{left:280px;width:250px;top:116px;font-family:"Bodoni Moda",serif;font-size:58px;line-height:1;color:var(--cyan);font-weight:500}
.cover-road{left:300px;width:220px;top:498px;font-size:8.5px;line-height:1.2;letter-spacing:2px;color:var(--cyan);font-weight:600}
.cover-where{left:300px;width:220px;top:510px;font-size:24px;line-height:1.2}
/* inside left */
.why-title{left:24px;width:230px;top:40px;font-size:10px;line-height:1.2;color:var(--gold)}
.why-brush{left:24px;width:230px;top:54px;font-size:22px;line-height:1.3;color:var(--cyan)}
.why-body{left:50px;width:178px;top:106px;font-family:"Quicksand",sans-serif;font-size:8.3px;line-height:1.55}
.verse{left:70px;width:140px;font-size:5.6px;font-style:italic;line-height:1.4}
.verse--a{top:272px}
.verse--b{top:343px}
.qm-l{left:30px}
.qm-r{left:218px}
/* inside right */
.way-small{left:300px;width:220px;top:40px;font-size:10.5px;line-height:1.2;color:var(--yellow)}
.way-brush{left:290px;width:230px;top:50px;font-size:42px;line-height:1.2;color:var(--white)}
.truths{left:285px;width:245px;top:112px;list-style:none}
.truth{padding:6px 22px 5px;margin-bottom:6px;background:linear-gradient(90deg,rgba(40,200,240,.25),rgba(40,210,245,.55) 50%,rgba(40,200,240,.25));font-size:5.5px;line-height:1.35;font-style:italic;color:var(--ink)}
.truth b{display:block;font-style:normal;font-size:6.5px;margin-top:3px}
.prayer{left:294px;top:412px;width:246px;height:162px;background:var(--white);clip-path:polygon(0 14%,6% 4%,10% 10%,16% 0,22% 8%,30% 3%,38% 10%,46% 2%,55% 9%,63% 3%,72% 10%,80% 4%,88% 11%,95% 5%,100% 10%,100% 100%,0 100%)}
.prayer-head{left:294px;width:246px;top:440px;font-size:22px;line-height:1.2;color:var(--ink)}
.prayer-body{left:310px;width:214px;top:474px;font-size:5.8px;line-height:1.45;color:#222}
.prayer-body strong{color:var(--ink)}
</style>
</head>
<body>

<section class="spread spread--outside" aria-label="Outside spread: back panel and front cover">
  <div class="photo photo--farm" role="img" aria-label="Photo of a Midwest farm with red barns and cattle grazing on green pasture"></div>
  <div class="photo photo--gate" role="img" aria-label="Photo of a winding white road rising through clouds to a bright open gateway in the sky"></div>

  <div class="column column--back"></div>
  <h2 class="abs caps center back-title">Your Journey Continues</h2>
  <p class="abs script center back-script">Congratulations</p>
  <p class="abs center back-intro">If you have accepted Jesus as your Savior, you are now on the path to heaven. What's next?</p>
  <ul class="abs steps center">
    <li class="step"><h3>Read the Bible</h3><p>Start with the book of John to learn more about Jesus.</p></li>
    <li class="step"><h3>Pray Daily</h3><p>Talk to God as you would a friend</p></li>
    <li class="step"><h3>Find a Church</h3><p>Join a community of believers who can support and guide you.</p></li>
    <li class="step"><h3>Share the Good News</h3><p>Talk to God as you would a friend</p></li>
  </ul>
  <div class="abs contact center">
    <p class="lead">If you have questions or want more resources, reach out to us at:</p>
    <div class="row"><svg width="6" height="6" viewBox="0 0 10 10"><path d="M2 1l2 2-1 1.5a6 6 0 0 0 2.5 2.5L7 6l2 2-1.5 1.5C4 9 1 6 .5 2z" fill="var(--cyan)"/></svg>555 0147 2286</div>
    <div class="row"><svg width="6" height="5" viewBox="0 0 10 8"><rect x="0" y="0" width="10" height="8" rx="1" fill="var(--cyan)"/><path d="M0 0l5 4 5-4" stroke="var(--deep)" fill="none"/></svg>hello@brightskiestrail.org</div>
    <div class="row"><svg width="5" height="7" viewBox="0 0 8 11"><path d="M4 0a4 4 0 0 1 4 4c0 3-4 7-4 7S0 7 0 4a4 4 0 0 1 4-4z" fill="var(--cyan)"/><circle cx="4" cy="4" r="1.5" fill="var(--deep)"/></svg>Address 27 Meadow Lane, Fairview Ridge<br><b>ZIP: 0418830</b></div>
  </div>
  <span class="abs quote-mark" style="left:40px;top:384px">“</span>
  <span class="abs quote-mark" style="left:208px;top:404px">”</span>
  <p class="abs center back-verse">I have come that they may have life, &amp; have it to the full.<br><span class="ref">– John 10:10</span></p>

  <p class="abs caps center cover-top">A Lantern Trail</p>
  <p class="abs script center cover-bright">Bright</p>
  <p class="abs caps center cover-toward">Toward</p>
  <p class="abs center cover-skies">Skies</p>
  <p class="abs center cover-road">THE ROAD STARTS</p>
  <p class="abs script center cover-where">Right where you are</p>
</section>

<section class="spread spread--inside" aria-label="Inside spread">
  <div class="photo photo--fair" role="img" aria-label="Aerial photo of a busy county fairground with colorful tents and rides"></div>

  <div class="column column--why"></div>
  <h2 class="abs caps center why-title">Why Ask About</h2>
  <p class="abs brush center why-brush">heaven?</p>
  <p class="abs center why-body">Many people wonder about life after death. Is there a heaven? How can you be sure you'll get there? The good news is that God has provided clear answers in the Bible. Heaven is not just a destination; it's a promise for those who choose the right path.</p>
  <span class="abs quote-mark qm-l" style="top:258px">“</span>
  <span class="abs quote-mark qm-r" style="top:258px">”</span>
  <p class="abs center verse verse--a">For God so loved the world that he gave his one and only Son, that whoever believes in him shall not perish but have eternal life<br><span class="ref">– John 3:16</span></p>
  <span class="abs quote-mark qm-l" style="top:330px">“</span>
  <span class="abs quote-mark qm-r" style="top:330px">”</span>
  <p class="abs center verse verse--b">Jesus answered, 'I am the way and the truth and the life. No one comes to the Father except through me.<br><span class="ref">– John 14:6</span></p>

  <p class="abs caps center way-small">The Way To</p>
  <p class="abs brush center way-brush">heaven</p>
  <ul class="abs truths center">
    <li class="truth">Acknowledge Your Need: We all fall short of God's perfect standard. "For all have sinned and fall short of the glory of God"<b>Romans 3:23</b></li>
    <li class="truth">Believe in Jesus Christ: Jesus died on the cross to take the punishment for your sins. "But God demonstrates his own love for us in this: While we were still sinners, Christ died for us."<b>Romans 5:8</b></li>
    <li class="truth">Accept God's Gift of Salvation: Eternal life is a free gift, not something you can earn. "For it is by grace you have been saved, through faith and this is not from yourselves, it is the gift of God"<b>Ephesians 2:8-9</b></li>
    <li class="truth">Confess and Commit: Pray and invite Jesus into your life as your Savior. "If you declare with your mouth, 'Jesus is Lord,' and believe in your heart that God raised him from the dead, you will be saved"<b>Romans 10:9</b></li>
  </ul>

  <div class="abs prayer"></div>
  <p class="abs script center prayer-head">Dear God</p>
  <p class="abs center prayer-body">I know I have sinned and need your forgiveness. I believe Jesus died for my sins and rose from the dead. I trust Him as my Savior and commit my life to Him.<br><strong>Thank you for your grace and the gift of eternal life. Amen</strong></p>
</section>

</body>
</html>
```